Local fast-growing company in the service sector

We are looking for a modern business card design, which should also appear on our letterheads

Target Market(s)

Private and industrial sectors

Contact Information for Business Card

Vorname Name
Kellberger Str. 18
70865 Brunnfeld
Tel.: 07146-839214-0
Name@agentur-kvtl.de

Colors
9d9d9d
919191
aaaaaa

Requirements
Must have
• The logo (file) in silver

```html
<!DOCTYPE html>
<html lang="de">
<head>
<meta charset="utf-8">
<title>KVTL Visitenkarte</title>
<link rel="stylesheet" href="https://fonts.googleapis.com/css2?family=Mulish:wght@400;600;700&display=swap">
<style>
  :root {
    --stage: #2b2b2c;
    --paper: #ffffff;
    --silver-light: #c9cacc;
    --silver-mid: #9d9d9d;
    --silver-dark: #6f7072;
    --brand-grey: #919191;
    --text-light: #f2f2f2;
    --text-soft: #e4e4e4;
  }
  * { margin: 0; padding: 0; box-sizing: border-box; }
  html, body { width: 1200px; height: 960px; overflow: hidden; }
  body {
    background: var(--stage);
    font-family: "Mulish", Arial, sans-serif;
    position: relative;
  }
  .card {
    position: absolute;
    width: 600px;
    height: 342px;
    border-radius: 22px;
    overflow: hidden;
    box-shadow: 0 4px 10px rgba(0,0,0,0.45);
  }
  .card-front { left: 302px; top: 129px; }
  .card-back {
    left: 299px; top: 488px;
    background: linear-gradient(90deg, #c6c7c9 0%, #acadaf 45%, #7e7f81 100%);
  }
  .card-surface { position: absolute; inset: 0; }
  .brand-lockup {
    position: absolute;
    left: 46px; top: 142px;
    display: flex; align-items: center; gap: 12px;
  }
  .brand-mark-square {
    width: 40px; height: 40px;
    background: var(--brand-grey);
  }
  .brand-name {
    font-weight: 700;
    font-size: 46px;
    line-height: 1;
    color: var(--brand-grey);
    letter-spacing: 1px;
  }
  .contact {
    position: absolute;
    right: 38px; top: 108px;
    text-align: right;
    color: var(--text-soft);
  }
  .contact-name {
    font-size: 25px; font-weight: 700;
    color: var(--text-light);
    margin-bottom: 3px;
    letter-spacing: 0.3px;
  }
  .contact-address { font-size: 14px; line-height: 18px; margin-bottom: 6px; }
  .contact-line {
    display: flex; justify-content: flex-end; align-items: center; gap: 7px;
    font-size: 14px; line-height: 19px;
  }
  .contact-line svg { width: 13px; height: 13px; fill: var(--text-light); }
  .back-name {
    position: absolute;
    left: 0; right: 0; top: 118px;
    text-align: center;
    font-weight: 700;
    font-size: 84px;
    line-height: 1;
    color: #8a8b8d;
    letter-spacing: 2px;
  }
  .back-url {
    position: absolute;
    left: 0; right: 0; top: 289px;
    text-align: center;
    font-size: 15px;
    letter-spacing: 3px;
    color: var(--text-light);
  }
</style>
</head>
<body>
  <section class="card card-front">
    <svg class="card-surface" width="600" height="342" viewBox="0 0 600 342">
      <defs>
        <radialGradient id="frontGlow" cx="0.55" cy="0.5" r="0.75">
          <stop offset="0" stop-color="#d9d9da"/>
          <stop offset="0.45" stop-color="#9d9d9d"/>
          <stop offset="1" stop-color="#6a6b6d"/>
        </radialGradient>
        <linearGradient id="chevronEdge" x1="0" y1="0" x2="0" y2="1">
          <stop offset="0" stop-color="#e6e6e7"/>
          <stop offset="0.5" stop-color="#aaaaaa"/>
          <stop offset="1" stop-color="#d2d2d3"/>
        </linearGradient>
      </defs>
      <rect width="600" height="342" fill="url(#frontGlow)"/>
      <path d="M0 0 H214 L350 145 Q362 171 350 197 L214 342 H0 Z" fill="url(#chevronEdge)"/>
      <path d="M0 0 H198 L338 145 Q350 171 338 197 L198 342 H0 Z" fill="var(--paper)"/>
    </svg>

    <div class="brand-lockup">
      <span class="brand-mark-square"></span>
      <span class="brand-name">KVTL</span>
    </div>

    <div class="contact">
      <p class="contact-name">Vorname Name</p>
      <p class="contact-address">Kellberger Str. 18<br>70865 Brunnfeld</p>
      <p class="contact-line">07146-839214-0
        <svg viewBox="0 0 16 16"><path d="M3.6 1.2l2.3 2.6-1.3 1.9c.9 2 2.5 3.6 4.6 4.6l1.9-1.3 2.6 2.3-1.1 2.2C7.3 14.8 1.2 8.7 1.4 2.3z"/></svg>
      </p>
      <p class="contact-line">Name@agentur-kvtl.de
        <svg viewBox="0 0 16 16"><path d="M1 3h14v1.2L8 8.6 1 4.2z M1 5.6l7 4.4 7-4.4V13H1z"/></svg>
      </p>
      <p class="contact-line">www.agentur-kvtl.de
        <svg viewBox="0 0 16 16"><circle cx="8" cy="8" r="7"/><path d="M5 4.5c1.5.5 2 1.5 1 2.5s.5 2 1.5 2.5-.5 2.5.5 3.5M10.5 3c-.5 1.5.5 2.5 2 2.5" stroke="#8a8b8d" stroke-width="1.2" fill="none"/></svg>
      </p>
    </div>
  </section>

  <section class="card card-back">
    <p class="back-name">KVTL</p>
    <p class="back-url">WWW.AGENTUR-KVTL.DE</p>
  </section>
</body>
</html>
```